Marlowe Group needs a business card

I would like the card to be simple but modern and elegant.
I like black and white.
or black and gold.
we are a private finance lender and also are involved in property and property developments.

please look at the business card photos i provided i would like M.G only one one side and all the other details on the other side use fonts that tie in with my theme.

Industry/Entity Type

Finance

Contact Information for Business Card

Marlowe Group (M.G) Daniel Marlowe M: 0413586207 E: danmarl@inboxmail.test

Font styles to use
Other font styles liked:
• Use fonts that would reflect our business

Colors
000000
ffffff

Requirements
Must have
• one side of details
• other side has either M.G or Marlowe Group like in the photos provided

```html
<!DOCTYPE html>
<html lang="en">
<head>
<meta charset="UTF-8">
<title>Marlowe Group – Business Card</title>
<link rel="stylesheet" href="https://fonts.googleapis.com/css2?family=Exo+2:wght@300;400;600;700&display=swap">
<style>
  :root {
    --backdrop: #4a4a4a;
    --card: #000000;
    --ink: #ffffff;
    --rule: #d9d9d9;
  }
  * { margin: 0; padding: 0; box-sizing: border-box; }
  html, body {
    width: 1200px;
    height: 796px;
    overflow: hidden;
    background: var(--backdrop);
  }
  .canvas {
    position: relative;
    width: 1200px;
    height: 796px;
    display: flex;
    justify-content: center;
    align-items: center;
    gap: 80px;
  }
  .card {
    width: 360px;
    height: 560px;
    background: var(--card);
    color: var(--ink);
    position: relative;
    box-shadow: 0 18px 40px rgba(0, 0, 0, 0.45);
    font-family: "Exo 2", sans-serif;
  }
  .card-front .monogram {
    position: absolute;
    top: 150px;
    left: 0;
    right: 0;
    text-align: center;
    font-weight: 400;
    font-size: 64px;
    letter-spacing: 2px;
  }
  .card-back .company {
    position: absolute;
    top: 52px;
    right: 30px;
    font-weight: 700;
    font-size: 36px;
    letter-spacing: 0.5px;
    white-space: nowrap;
  }
  .details {
    position: absolute;
    left: 28px;
    right: 28px;
    top: 322px;
  }
  .details .name {
    text-align: right;
    padding-right: 6px;
    font-weight: 600;
    font-size: 27px;
    letter-spacing: 1px;
    padding-bottom: 8px;
    white-space: nowrap;
  }
  .details .rule {
    height: 1.5px;
    background: var(--rule);
  }
  .details .phone {
    text-align: center;
    font-weight: 300;
    font-size: 20px;
    letter-spacing: 2px;
    padding: 10px 0 8px;
  }
  .details .email {
    font-weight: 300;
    font-size: 20px;
    letter-spacing: 0.5px;
    padding: 10px 0 8px;
    white-space: nowrap;
  }
</style>
</head>
<body>
  <main class="canvas">
    <section class="card card-front" aria-label="Card front">
      <div class="monogram">M.G</div>
    </section>
    <section class="card card-back" aria-label="Card back">
      <div class="company">Marlowe Group</div>
      <div class="details">
        <div class="name">Daniel Marlowe</div>
        <div class="rule"></div>
        <div class="phone">0413586207</div>
        <div class="rule"></div>
        <div class="email">danmarl@inboxmail.test</div>
        <div class="rule"></div>
      </div>
    </section>
  </main>
</body>
</html>
```